QuillNest.com how-it-works animated video

We need a video animation and illustrations for the QuillNest.com home page that show how our knowledge automation framework works.

Please read https://www.quillnest.example/knowledge-is-stories and see https://www.quillnest.example/home and for more information.

I strongly advise to follow the 5 minute quick start at https://www.quillnest.example/quick-start before you start.

Target Market(s)

Professionals. Early adopters.

Industry/Entity Type

Information Technology

Font styles to use
Other font styles liked:
• Roboto

Colors

Designer to choose colors to be used in the design.

Requirements
Must have
• The animation/ilustrations must be easy to understand, match our design style and illustrate the following 6 activities of Experts, Constructs, and Consumers:
• 1) experts automating their knowledge by designing flow charts for free
• 2) flow charts are turned into constructs (robots) for free
• 3) constructs being published to the public stage for free
• 4) consumers starting sessions with constructs for free
• 5) constructs being published to the public stage for a small fee
• 6) consumers starting sessions with constructs for a small free
• 7) low cost organizational membership where constructs can shared within groups
Nice to have
• Flat Design Style
• See attached color scheme #235B7B #86BBD8 #A1E8AF #B5BEC6 #F6AE2D

```html
<!DOCTYPE html>
<html lang="en">
<head>
<meta charset="utf-8">
<title>Expert profile</title>
<link href="https://fonts.googleapis.com/css2?family=Roboto:wght@300;400;700&display=swap" rel="stylesheet">
<style>
  :root {
    --brand-blue: #235B7B;
    --text-blue: #2b5f7e;
    --canvas-bg: #ffffff;
  }
  * { margin: 0; padding: 0; box-sizing: border-box; }
  html, body {
    width: 1200px;
    height: 675px;
    overflow: hidden;
    background: var(--canvas-bg);
  }
  .canvas {
    position: relative;
    width: 1200px;
    height: 675px;
    font-family: "Roboto", Arial, sans-serif;
    color: var(--brand-blue);
  }
  .expert-figure {
    position: absolute;
    left: 162px;
    top: 103px;
    width: 180px;
    height: 486px;
    background: var(--brand-blue);
    border-radius: 6px;
    box-shadow: -4px 6px 10px rgba(0, 0, 0, 0.25);
  }
  .profile-rules {
    position: absolute;
    left: 0;
    top: 0;
  }
  .profile-title {
    position: absolute;
    right: 472px;
    top: 168px;
    font-weight: 700;
    font-size: 21px;
    letter-spacing: 0.2px;
  }
  .profile-field {
    position: absolute;
    right: 472px;
    top: 234px;
    font-weight: 400;
    font-size: 21px;
  }
  .profile-bio {
    position: absolute;
    left: 403px;
    top: 291px;
    width: 325px;
    font-weight: 300;
    font-size: 12.7px;
    line-height: 16.45px;
    text-align: justify;
    color: var(--text-blue);
  }
</style>
</head>
<body>
<main class="canvas">
  <div class="expert-figure" role="img" aria-label="Flat illustration of a standing expert in a suit"></div>

  <svg class="profile-rules" width="1200" height="675" viewBox="0 0 1200 675" aria-hidden="true">
    <g stroke="var(--brand-blue)" stroke-width="2" fill="none">
      <line x1="753" y1="162" x2="753" y2="201"/>
      <line x1="403" y1="213" x2="745" y2="213"/>
      <rect x="749.5" y="208.5" width="7" height="7" transform="rotate(45 753 212)" fill="#fff"/>
      <line x1="753" y1="223" x2="753" y2="263"/>
      <rect x="750.5" y="269.5" width="5" height="7" fill="#fff"/>
      <line x1="753" y1="284" x2="753" y2="526"/>
    </g>
  </svg>

  <h1 class="profile-title">EXPERT</h1>
  <h2 class="profile-field">Field of expertise</h2>
  <p class="profile-bio">Lorem ipsum dolor sit amet, consectetuer adipiscing elit. Etiam cursus purus interdum libero. Nuncanto metus. Vestibulum ante ipsum primis in faucibus orci luctus et ultrices posuere cubilia Curae; Vivamus eu orci. Pellentesque sit amet dui vel justo gravida auctor. Integer tempus malesuada pede. Morbi urna. Vestibulum ante ipsum primis in faucibus orci luctus et ultrices posuere cubilia Curae; Suspendisse potenti. Pellentesque tempor. Ut venenatis. Praesent aliquet, neque pretium congue mattis, ipsum augue dignissim ante, ac pretium nisl lectus at magna. In hac habitasse platea dictumst. Morbi turpis arcu, egestas congue, condimentum quis, tristique cursus, leo. Vivamus feugiat.</p>
</main>
</body>
</html>
```